Velvet Dice Night Age Verification Landing Page

To create a visually appealing design for the landing page of the adult game "Velvet Dice Night" that confirms the visitor's age.
The design should have a simple and visually appealing look that focuses on two buttons labeled "Yes" and "No". The purpose of the page is to confirm that the visitor is 18 years of age or older before accessing the game's content. Responsive design that works well on desktop and mobile devices. The final output should be delivered in PSD, AI, or Sketch format, along with any necessary images or assets.
I have also attached examples.

```html
<!DOCTYPE html>
<html lang="en">
<head>
<meta charset="UTF-8">
<title>Velvet Dice Night — Age Verification</title>
<link href="https://fonts.googleapis.com/css2?family=Inter:wght@400;700&family=Kaushan+Script&display=swap" rel="stylesheet">
<style>
  :root {
    --bg-deep: #141019;
    --bg-mid: #221d2b;
    --bg-haze: #2f3442;
    --violet: #7c3a96;
    --violet-soft: #9a5cb4;
    --violet-line: #8a4aa6;
    --panel: rgba(12, 6, 18, 0.86);
    --white: #ffffff;
    --photo-warm: #6a4a66;
    --photo-cool: #3a3d58;
  }
  * { box-sizing: border-box; margin: 0; padding: 0; }
  html, body { width: 1200px; height: 609px; overflow: hidden; }
  body {
    position: relative;
    font-family: "Inter", sans-serif;
    color: var(--white);
    background:
      radial-gradient(ellipse at 85% 70%, var(--bg-haze) 0%, transparent 55%),
      radial-gradient(ellipse at 15% 40%, var(--bg-mid) 0%, transparent 60%),
      var(--bg-deep);
  }
  .hero-photo {
    position: absolute;
    left: 437px; top: 0;
    width: 364px; height: 609px;
    background: radial-gradient(ellipse at 50% 35%, var(--photo-warm) 0%, var(--photo-cool) 55%, transparent 80%);
    opacity: 0.75;
  }
  .brand {
    position: absolute;
    left: 86px; top: 62px;
    display: flex; align-items: center; gap: 10px;
    font-size: 22px; font-weight: 700;
    color: var(--violet-soft);
  }
  .brand-dot {
    width: 14px; height: 14px; border-radius: 50%;
    background: var(--violet-soft);
  }
  .music-toggle {
    position: absolute;
    left: 1056px; top: 30px;
    width: 58px; height: 58px;
    border-radius: 15px;
    background: var(--violet);
    box-shadow: 0 6px 14px rgba(124, 58, 150, 0.45);
    display: flex; align-items: center; justify-content: center;
  }
  .age-modal {
    position: absolute;
    left: 333px; top: 195px;
    width: 534px; height: 335px;
    border-radius: 26px;
    background: var(--panel);
    box-shadow: 0 0 28px rgba(154, 92, 180, 0.55);
    text-align: center;
  }
  .modal-frame { position: absolute; inset: 0; }
  .flourish {
    position: absolute;
    left: 127px; width: 282px; height: 30px;
    background: linear-gradient(90deg, transparent, var(--violet-line) 20%, var(--violet-soft) 50%, var(--violet-line) 80%, transparent);
    opacity: 0.55;
    border-radius: 15px;
  }
  .flourish-top { top: 10px; }
  .flourish-bottom { top: 288px; height: 36px; }
  .side-ornament {
    position: absolute;
    top: 135px; width: 16px; height: 70px;
    background: linear-gradient(180deg, transparent, var(--violet-line), transparent);
    border-radius: 8px;
    opacity: 0.8;
  }
  .side-ornament-left { left: 13px; }
  .side-ornament-right { right: 13px; }
  .modal-title {
    position: absolute;
    left: 0; right: 0; top: 80px;
    font-family: "Kaushan Script", cursive;
    font-weight: 400;
    font-size: 40px;
    line-height: 1;
    white-space: nowrap;
  }
  .modal-text {
    position: absolute;
    left: 0; right: 0; top: 136px;
    font-size: 15.5px;
    line-height: 28px;
  }
  .choice {
    position: absolute;
    top: 217px;
    width: 109px; height: 45px;
    display: flex; align-items: center; justify-content: center; gap: 22px;
    font-size: 15px; font-weight: 700;
    border-radius: 3px;
    color: var(--white);
  }
  .choice-yes { left: 149px; background: var(--violet); }
  .choice-no { left: 275px; border: 2px solid var(--white); }
</style>
</head>
<body>
  <div class="hero-photo" role="img" aria-label="Photo of a model in a denim jacket behind the dialog"></div>

  <div class="brand"><span class="brand-dot"></span>Velvet Dice Night</div>

  <div class="music-toggle" aria-label="Toggle music">
    <svg width="26" height="26" viewBox="0 0 24 24" fill="#fff">
      <path d="M8 4.5 L20 2.5 V16.5 a3 3 0 1 1 -2 -2.8 V7 L10 8.4 V18.5 a3 3 0 1 1 -2 -2.8 Z"/>
    </svg>
  </div>

  <section class="age-modal">
    <svg class="modal-frame" width="534" height="335" viewBox="0 0 534 335" fill="none" stroke="#8a4aa6" stroke-width="1.2">
      <path d="M20 18 H85 M20 18 V72 M28 26 H70 M28 26 V60"/>
      <path d="M514 18 H449 M514 18 V72 M506 26 H464 M506 26 V60"/>
      <path d="M20 317 H85 M20 317 V263 M28 309 H70 M28 309 V275"/>
      <path d="M514 317 H449 M514 317 V263 M506 309 H464 M506 309 V275"/>
      <path d="M21 72 V135 M21 205 V263 M513 72 V135 M513 205 V263"/>
    </svg>
    <div class="flourish flourish-top" role="img" aria-label="Ornamental scroll flourish"></div>
    <div class="flourish flourish-bottom" role="img" aria-label="Ornamental scroll flourish"></div>
    <div class="side-ornament side-ornament-left" role="img" aria-label="Heart and spade ornament"></div>
    <div class="side-ornament side-ornament-right" role="img" aria-label="Heart and spade ornament"></div>

    <h1 class="modal-title">Velvet Dice Night</h1>
    <p class="modal-text">Confirm that the visitor is 18 years of age or<br>older before accessing the game's content.</p>

    <a class="choice choice-yes">YES
      <svg width="16" height="14" viewBox="0 0 16 14"><path d="M1.5 7.5 L6 12 L14.5 2" stroke="#fff" stroke-width="3" fill="none" stroke-linecap="round" stroke-linejoin="round"/></svg>
    </a>
    <a class="choice choice-no">NO
      <svg width="11" height="11" viewBox="0 0 11 11"><path d="M1.5 1.5 L9.5 9.5 M9.5 1.5 L1.5 9.5" stroke="#fff" stroke-width="2.6" stroke-linecap="round"/></svg>
    </a>
  </section>
</body>
</html>
```